Sickle Cell Patient Flyer

I need this be appealing to families dealing with sickle cell disease. Both informative-introducing the idea that a stroke prevention program is not only easy for their children but necessary. Stroke is a risk to all with children with SCD.
I included a few info flyers from the Vessel Alliance and licensed to me photos I like. I am open to suggestions.
web address is brightpathwellbeing.net
Call to schedule 833-412-7086
TCD is a safe and accurate tool that makes stroke prevention possible for your SCD patients and family.
Risk is highest for SCD sufferers age 2 to 5. Protect your childs future.

Target Market(s)

Parents, families and medical professionals

Industry/Entity Type

Medical wellness

Font styles to use
Other font styles liked:
• something close to my logo font

Colors
0094D4
00A9DD
6FCCEA
C7EBF8
E9F6FB

Requirements
Nice to have
• pictures of kids (Children of color) pictures of Brains, kids happy with medical professionals
Should not have
• dark colors

```html
<!DOCTYPE html>
<html lang="en">
<head>
<meta charset="utf-8">
<title>Stroke Prevention for Children with Sickle Cell Disease</title>
<link rel="stylesheet" href="https://fonts.googleapis.com/css2?family=Mystery+Quest&family=Poppins:wght@400;500;600;700&display=swap">
<style>
  :root {
    --stage: #b4b4b4;
    --paper: #ffffff;
    --navy: #0c3a78;
    --ink: #222831;
    --mint: #6fc6a0;
    --panel: #c8f5e6;
    --panel-line: #4a90d4;
    --sky: #3f95d8;
    --photo-dark: #1d3d4c;
    --photo-mid: #2c5566;
  }
  * { box-sizing: border-box; margin: 0; padding: 0; }
  html, body { width: 1200px; height: 2334px; overflow: hidden; }
  body {
    background: var(--stage);
    font-family: "Poppins", sans-serif;
    color: var(--ink);
    position: relative;
  }
  .flyer {
    position: absolute;
    left: 100px; top: 521px;
    width: 1000px; height: 1292px;
    background: var(--paper);
    overflow: hidden;
    box-shadow: 0 24px 40px rgba(0,0,0,.25);
  }
  .hero-art { position: absolute; left: 0; top: 0; width: 1000px; height: 640px; }
  .brand {
    position: absolute; left: 62px; top: 92px;
    display: flex; align-items: center; gap: 14px;
  }
  .brand-mark { width: 40px; height: 40px; border-radius: 50%; background: var(--mint); }
  .brand-name {
    font-family: "Poppins", sans-serif; font-weight: 700;
    font-size: 36px; line-height: 1.1; color: var(--navy); width: 260px;
  }
  .kicker {
    position: absolute; left: 63px; top: 250px;
    font-weight: 600; font-size: 30px; line-height: 1.12; color: var(--ink);
  }
  .headline {
    position: absolute; left: 62px; top: 320px;
    font-family: "Mystery Quest", cursive; font-weight: 400;
    font-size: 70px; line-height: 1.0; color: var(--navy);
  }
  .intro {
    position: absolute; left: 66px; top: 530px;
    padding-left: 14px; border-left: 3px solid var(--mint);
    font-size: 22px; line-height: 1.25; color: var(--ink);
  }
  .badge {
    position: absolute; left: 462px; top: 345px;
    width: 200px; height: 200px; border-radius: 50%;
    background: var(--navy); border: 5px solid var(--paper);
    color: #fff; text-align: center;
    display: flex; flex-direction: column; justify-content: center;
    font-weight: 600; font-size: 20px; line-height: 1.22;
  }
  .badge strong { color: var(--mint); font-size: 32px; font-weight: 700; }
  .benefits {
    position: absolute; left: 62px; top: 665px;
    width: 876px; height: 355px;
    background: var(--panel); border: 2px solid var(--panel-line); border-radius: 14px;
  }
  .benefits-title {
    position: absolute; left: 110px; top: 645px; width: 780px; height: 74px;
  }
  .benefits-title span {
    position: absolute; inset: 0; display: flex; align-items: center; justify-content: center;
    font-family: "Mystery Quest", cursive; font-size: 50px; color: var(--mint);
  }
  .benefit {
    position: absolute; top: 735px; width: 280px; text-align: center;
    font-size: 22px; line-height: 1.25; color: var(--ink);
  }
  .benefit svg { display: block; margin: 0 auto 22px; }
  .divider {
    position: absolute; top: 745px; height: 262px;
    border-left: 2px dashed var(--panel-line);
  }
  .notice {
    position: absolute; left: 62px; top: 1037px; width: 876px; height: 90px;
    background: var(--navy); border-radius: 14px;
    display: flex; align-items: center; justify-content: center; text-align: center;
    color: #fff; font-weight: 600; font-size: 25px; line-height: 1.2;
    box-shadow: 0 8px 10px rgba(0,0,0,.15);
  }
  .contact { position: absolute; left: 62px; top: 1158px; }
  .contact-label { font-weight: 600; font-size: 28px; color: var(--sky); }
  .contact-phone {
    display: flex; align-items: center; gap: 8px;
    font-weight: 600; font-size: 40px; color: var(--ink); line-height: 1.1;
  }
  .sep { position: absolute; top: 1196px; height: 40px; border-left: 2px solid #888; }
  .web { position: absolute; left: 458px; top: 1192px; font-weight: 500; font-size: 18px; line-height: 1.35; }
  .web div { display: flex; align-items: center; gap: 8px; }
  .social { position: absolute; left: 825px; top: 1192px; font-weight: 500; font-size: 18px; text-align: center; }
  .social-dots { display: flex; gap: 5px; justify-content: center; margin-top: 2px; }
  .social-dots i { width: 15px; height: 15px; border-radius: 50%; background: var(--navy); display: block; }
</style>
</head>
<body>
  <main class="flyer">
    <svg class="hero-art" viewBox="0 0 1000 640">
      <defs>
        <radialGradient id="photoTone" cx="0.6" cy="0.45" r="0.6">
          <stop offset="0" stop-color="#2f5a6a"/>
          <stop offset="1" stop-color="#1b3a48"/>
        </radialGradient>
      </defs>
      <circle cx="890" cy="200" r="440" fill="none" stroke="var(--mint)" stroke-width="22"/>
      <circle cx="880" cy="200" r="406" fill="#fff"/>
      <circle cx="880" cy="200" r="400" fill="url(#photoTone)" role="img" aria-label="Photo of a smiling child in a yellow top raising both arms, with chalk brain drawings on a dark board"/>
    </svg>

    <div class="brand" aria-label="BrightPath Wellbeing">
      <span class="brand-mark"></span>
      <span class="brand-name">BrightPath Wellbeing</span>
    </div>

    <p class="kicker">STROKE PREVENTION<br>FOR CHILDREN WITH</p>
    <h1 class="headline">SICKLE CELL<br>DISEASE<br>IS POSSIBLE!</h1>
    <p class="intro">TCD is a safe and accurate tool<br>that makes stroke prevention possible<br>for your SCD patients and family.</p>

    <div class="badge">Stroke is a risk<br>to all with<br>children with<br><strong>SCD</strong></div>

    <section class="benefits"></section>
    <div class="benefits-title">
      <svg width="780" height="74" viewBox="0 0 780 74"><path d="M0 0 H780 L740 74 H40 Z" fill="var(--navy)"/></svg>
      <span>PROTECT YOUR CHILDS FUTURE</span>
    </div>

    <div class="benefit" style="left:60px">
      <svg width="104" height="104" viewBox="0 0 104 104">
        <circle cx="52" cy="52" r="50" fill="var(--navy)" stroke="var(--panel-line)" stroke-width="3"/>
        <path d="M38 78 V66 C28 60 26 44 34 34 C44 22 66 24 72 38 C74 44 74 48 78 54 L72 56 V64 C72 68 68 70 62 69 V78" fill="none" stroke="#fff" stroke-width="3" stroke-linejoin="round"/>
        <path d="M42 42 C46 36 56 36 60 42 M46 50 C52 46 58 48 62 52" fill="none" stroke="#fff" stroke-width="2.5"/>
      </svg>
      Simple and<br>painless screening<br>for your child
    </div>
    <div class="divider" style="left:338px"></div>
    <div class="benefit" style="left:355px">
      <svg width="104" height="104" viewBox="0 0 104 104">
        <circle cx="52" cy="52" r="50" fill="var(--navy)" stroke="var(--panel-line)" stroke-width="3"/>
        <g fill="none" stroke="#fff" stroke-width="3">
          <ellipse cx="40" cy="36" rx="9" ry="6"/><ellipse cx="64" cy="40" rx="8" ry="6"/>
          <ellipse cx="38" cy="62" rx="9" ry="7"/><ellipse cx="62" cy="64" rx="11" ry="8" transform="rotate(-30 62 64)"/>
        </g>
      </svg>
      About 11% of SCD<br>patients have strokes<br>before age 20 with<br>The highest risk<br>between age 2 and 5
    </div>
    <div class="divider" style="left:645px"></div>
    <div class="benefit" style="left:650px">
      <svg width="104" height="104" viewBox="0 0 104 104">
        <circle cx="52" cy="52" r="50" fill="var(--navy)" stroke="var(--panel-line)" stroke-width="3"/>
        <g fill="none" stroke="#fff" stroke-width="3">
          <rect x="30" y="28" width="44" height="34" rx="3"/><path d="M38 54 C40 42 64 42 66 54"/>
          <path d="M46 62 V70 M58 62 V70 M36 72 H68"/>
        </g>
      </svg>
      Our Screening uses<br>ultrasound which is<br>transcranial<br>doppler
    </div>

    <div class="notice">Screening or early signs of stroke can be a tool to for early<br>diagnosis allowing for treatments that eliminate the risk</div>

    <div class="contact">
      <div class="contact-label">Call to schedule</div>
      <div class="contact-phone">
        <svg width="32" height="32" viewBox="0 0 32 32"><circle cx="16" cy="16" r="15" fill="var(--mint)"/><path d="M11 8 L14 12 L12 14 C13 17 15 19 18 20 L20 18 L24 21 L22 24 C15 24 8 17 8 10 Z" fill="#fff"/></svg>
        833-412-7086
      </div>
    </div>
    <div class="sep" style="left:432px"></div>
    <div class="web">
      <div><svg width="14" height="11" viewBox="0 0 14 11"><rect width="14" height="11" fill="var(--mint)"/><path d="M0 0 L7 6 L14 0" fill="none" stroke="#fff" stroke-width="1.5"/></svg>info@brightpathwellbeing.net</div>
      <div><svg width="14" height="14" viewBox="0 0 14 14"><circle cx="7" cy="7" r="6" fill="none" stroke="var(--mint)" stroke-width="2"/><path d="M1 7 H13 M7 1 C3 5 3 9 7 13 C11 9 11 5 7 1" fill="none" stroke="var(--mint)" stroke-width="1.2"/></svg>www.brightpathwellbeing.net</div>
    </div>
    <div class="sep" style="left:800px"></div>
    <div class="social">
      Follow us on
      <div class="social-dots"><i></i><i></i><i></i></div>
    </div>
  </main>
</body>
</html>
```